Modern Homepage Design for brenvik.nl – Fish & Chicken Food Webshop

Brenvik.nl is an online store that sells fish and chicken food. The design should be visually appealing, easy to navigate, and optimized for e-commerce. We want a layout that helps customers quickly find what they need and encourages them to explore our products.
A good example of the style and structure we like is dierkamp.nl – clean layout, clear product focus, and user-friendly navigation.
Brand Colors (must be used):
Orange: #f7a441
Dark Gray: #3c3c3b
White: #ffffff
Please use these colors consistently throughout the design.
Homepage Requirements:
The homepage should include the following sections:
Main Slider / Hero Banner
A large, eye-catching slider at the top of the page to highlight promotions or featured categories.
Category Blocks
A section with clear, clickable blocks or tiles that link to main product categories (e.g., Fish Food, Chicken Food, Accessories).
Featured Products
A section showcasing selected or best-selling products.
Special Offers / Promotions
A space to highlight current deals or limited-time offers.
Three Banners in a Row
A section with three horizontal banners side by side, which can be used for promotions, shipping info, or other key messages.
Unique Selling Points (USPs)
A section that briefly explains what makes our store different (e.g., fast delivery, high-quality feed, trusted by professionals).
SEO Content Block
A short paragraph of text for SEO purposes (use Lorem Ipsum for dummy content).
Footer Design
Include space for contact information, navigation links, and social media.
Design Notes:
The design must be responsive and mobile-friendly.
Focus on clean layout, good spacing, and easy navigation.
Use modern fonts and a clear visual hierarchy.
We are only looking for the homepage design at this stage, but we may work with the selected designer on additional pages later.
Deliverables:
Homepage design in layered PSD, Figma, or Adobe XD format
Any fonts and assets used
Preview images/mockups
We look forward to seeing your ideas and working with a designer who can bring our brand to life with a fresh and functional homepage design.
Let us know if you have any questions.
Hobby Animal Keepers, Pet Owners
Animal Nutrition & Feed
2 page

```html
<!DOCTYPE html>
<html lang="en">
<head>
<meta charset="utf-8">
<title>Brenvik.nl – Fish &amp; Chicken Feed</title>
<link href="https://fonts.googleapis.com/css2?family=Fugaz+One&family=Open+Sans:wght@400;600;700&display=swap" rel="stylesheet">
<style>
:root{
  --orange:#f7a441;
  --orange-deep:#e98a1c;
  --brown:#b7650f;
  --dark:#3c3c3b;
  --dark-2:#4a4a49;
  --white:#ffffff;
  --cream:#fbf0d8;
  --peach:#fde6c8;
  --text:#3c3c3b;
}
*{box-sizing:border-box;margin:0;padding:0}
html,body{width:1200px;height:3807px;overflow:hidden}
body{position:relative;font-family:"Open Sans",sans-serif;color:var(--text);background:var(--white)}
.abs{position:absolute}
.display{font-family:"Fugaz One",sans-serif;font-weight:400}
.btn{position:absolute;display:flex;align-items:center;justify-content:space-between;background:var(--orange);color:var(--dark);border-radius:20px;font-weight:700;font-size:14px;padding:0 5px 0 14px;height:36px}
.btn .arr{width:26px;height:26px;border-radius:50%;background:var(--white);display:flex;align-items:center;justify-content:center}
.btn .arr svg{width:14px;height:14px}
.eyebrow{position:absolute;width:100%;text-align:center;font-size:15px}
.sec-title{position:absolute;width:100%;text-align:center;font-size:44px;color:var(--brown)}
.ph{position:absolute}

/* hero */
.hero{position:absolute;left:0;top:0;width:1200px;height:610px;background:linear-gradient(120deg,#c8962a,#d9ac3f 55%,#c99a30);overflow:hidden}
.logo{position:absolute;display:flex;align-items:center;gap:6px;font-family:"Open Sans",sans-serif;font-weight:700;color:var(--white)}
.logo .dot{border:4px solid var(--white);border-radius:50%}
.nav{position:absolute;left:236px;top:37px;width:539px;height:35px;background:var(--cream);border-radius:18px;display:flex;align-items:center;gap:30px;padding-left:62px;font-size:15px;font-weight:600}
.nav .active{color:var(--brown)}
.search{position:absolute;left:819px;top:40px;width:198px;height:30px;background:var(--white);border-radius:6px;overflow:hidden}
.search span{position:absolute;left:12px;top:8px;font-size:10px;color:#aaa}
.search i{position:absolute;right:0;top:0;width:36px;height:30px;background:var(--orange);display:flex;align-items:center;justify-content:center}
.hero h1{position:absolute;left:65px;top:143px;width:520px;font-size:50px;line-height:62px;color:var(--white)}
.hero p{position:absolute;left:65px;top:333px;width:440px;font-size:15px;line-height:22px;color:var(--white)}
.circ-nav{position:absolute;width:30px;height:30px;border-radius:50%;display:flex;align-items:center;justify-content:center}

/* category */
.cat{position:absolute;width:240px;text-align:center}
.cat .ring{position:absolute;left:32px;top:0;width:176px;height:176px;border-radius:50%;border:3px solid var(--orange)}
.cat .img{position:absolute;left:30px;top:8px;width:172px;height:172px;border-radius:50%}
.cat h3{position:absolute;top:200px;width:100%;font-size:23px;font-weight:400}

/* best sellers */
.bests{position:absolute;left:0;top:1100px;width:1200px;height:814px;background:linear-gradient(180deg,#fdebd3,#fde3c3)}
.card{position:absolute;top:1268px;width:330px;height:378px;border-radius:8px;overflow:hidden}
.card .tag{position:absolute;left:18px;top:218px;font-size:20px;color:var(--orange)}
.card .name{position:absolute;left:18px;top:247px;font-size:15px;color:var(--white);font-weight:600}
.card .desc{position:absolute;left:18px;top:268px;font-size:11px;color:#e6e6e6}
.card .heart{position:absolute;right:12px;top:14px}

/* promo */
.promo{position:absolute;left:139px;top:1771px;width:922px;height:282px;border-radius:10px;background:linear-gradient(90deg,#7a7a78,#3c3c3b 45%,#4d4d4c);overflow:hidden}

/* banners */
.banner{position:absolute;top:2115px;height:218px;overflow:hidden;border-radius:4px}

/* usp */
.usp{position:absolute;left:0;top:2453px;width:1200px;height:540px;background:linear-gradient(180deg,#4c4c4b,#3c3c3b)}
.usp-card{position:absolute;width:292px;height:64px;background:var(--white);border-radius:4px}
.usp-card .ico{position:absolute;left:22px;top:16px;width:36px;height:33px;background:var(--orange);border-radius:4px;display:flex;align-items:center;justify-content:center}
.usp-card h4{position:absolute;left:74px;top:10px;font-size:17px;font-weight:600;width:200px;padding-bottom:4px;border-bottom:1px solid #ddd}
.usp-card small{position:absolute;left:74px;top:40px;font-size:10px;color:#777}

/* footer */
.footer{position:absolute;left:0;top:3348px;width:1200px;height:459px}
.fcol h5{font-size:15px;font-weight:700;color:var(--white);margin-bottom:14px}
.fcol a,.fcol li{display:block;font-size:11px;color:var(--white);margin-bottom:11px;list-style:none}
.field{width:190px;background:#ececec;border-radius:3px;font-size:9px;color:#888;padding:5px 8px;margin-bottom:8px}
</style>
</head>
<body>

<!-- ===== HERO ===== -->
<section class="hero" role="img" aria-label="Sunlit golden grass field background">
</section>
<svg class="abs" style="left:0;top:440px" width="1200" height="180" viewBox="0 0 1200 180" aria-hidden="true">
  <path d="M0 115 C250 160 520 150 760 80 C960 20 1100 40 1200 75 L1200 180 L0 180Z" fill="var(--orange)"/>
  <path d="M0 150 C300 175 560 170 800 115 C980 75 1110 90 1200 170 L1200 180 L0 180Z" fill="var(--white)"/>
</svg>
<div class="ph" role="img" aria-label="Three bags of poultry feed with hens standing beside them" style="left:625px;top:135px;width:515px;height:370px;border-radius:12px;background:linear-gradient(90deg,#d7b24a,#e9e6e0 40%,#e9e6e0 60%,#2f5f4e 80%,#8a4a1e)"></div>

<div class="logo" style="left:63px;top:36px;font-size:32px"><span class="dot" style="width:30px;height:30px"></span>Brenvik</div>
<nav class="nav"><span class="active">Home</span><span>Category ⌄</span><span>Products</span><span>USPs</span><span>Contact Us</span></nav>
<div class="search"><span>Search</span><i><svg width="16" height="16" viewBox="0 0 24 24" fill="none" stroke="#3c3c3b" stroke-width="2.5"><circle cx="10" cy="10" r="7"/><path d="M15 15l6 6"/></svg></i></div>
<svg class="abs" style="left:1047px;top:46px" width="96" height="18" viewBox="0 0 96 18" fill="none" stroke="#fff" stroke-width="1.6" aria-hidden="true">
  <path d="M1 3h3l2 9h9l2-7H6"/><circle cx="8" cy="15" r="1.3"/><circle cx="14" cy="15" r="1.3"/>
  <circle cx="38" cy="6" r="3.5"/><path d="M32 16c1-4 11-4 12 0"/>
  <circle cx="64" cy="9" r="7"/><path d="M57 9h14M64 2c-3 4-3 10 0 14M64 2c3 4 3 10 0 14"/>
  <text x="74" y="13" fill="#fff" stroke="none" font-size="11" font-family="Open Sans">El</text>
</svg>

<h1 class="display hero-title" style="position:absolute;left:65px;top:143px;width:520px;font-size:50px;line-height:62px;color:#fff">From Chick to Hen – Complete Nutrition</h1>
<p style="position:absolute;left:65px;top:333px;width:440px;font-size:15px;line-height:22px;color:#fff">Give your flock the best — balanced, high-quality feed that supports healthy growth and consistent egg production</p>
<a class="btn" style="left:65px;top:406px;width:197px">Shop Chicken Food<span class="arr"><svg viewBox="0 0 16 16" fill="none" stroke="#3c3c3b" stroke-width="1.6"><path d="M2 8h11M9 4l4 4-4 4"/></svg></span></a>
<span class="circ-nav" style="left:66px;top:474px;border:2px solid #fff"><svg width="12" height="12" viewBox="0 0 12 12" fill="none" stroke="#fff" stroke-width="1.8"><path d="M8 2L4 6l4 4"/></svg></span>
<span class="circ-nav" style="left:104px;top:474px;background:var(--orange)"><svg width="12" height="12" viewBox="0 0 12 12" fill="none" stroke="#fff" stroke-width="1.8"><path d="M4 2l4 4-4 4"/></svg></span>

<!-- ===== CATEGORY ===== -->
<div class="eyebrow" style="top:654px;color:var(--orange)">Category</div>
<h2 class="sec-title display" style="top:673px">Shop by Category</h2>

<div class="cat" style="left:181px;top:748px">
  <div class="img" role="img" aria-label="Goldfish swimming above fish food pellets" style="background:radial-gradient(circle at 60% 50%,#f0902a,#c9c2a8 60%,#8a8d6a)"></div>
  <div class="ring"></div>
  <h3 style="top:198px">Fish Food</h3>
</div>
<div class="cat" style="left:480px;top:745px">
  <div class="img" role="img" aria-label="Chicken pecking at scattered grain" style="background:radial-gradient(circle at 60% 50%,#8a5a3a,#4a3a30 60%,#2a2420)"></div>
  <div class="ring"></div>
  <h3 style="top:201px">Chicken Food</h3>
</div>
<div class="cat" style="left:783px;top:748px">
  <div class="img" role="img" aria-label="Sack and scoop of grain feed" style="background:radial-gradient(circle at 45% 55%,#c89a5a,#8a6a4a 60%,#3a3430)"></div>
  <div class="ring"></div>
  <h3 style="top:198px">Accessories</h3>
</div>
<a class="btn" style="left:234px;top:1000px;width:127px">Shop Now<span class="arr"><svg viewBox="0 0 16 16" fill="none" stroke="#3c3c3b" stroke-width="1.6"><path d="M2 8h11M9 4l4 4-4 4"/></svg></span></a>
<a class="btn" style="left:536px;top:1000px;width:127px">Shop Now<span class="arr"><svg viewBox="0 0 16 16" fill="none" stroke="#3c3c3b" stroke-width="1.6"><path d="M2 8h11M9 4l4 4-4 4"/></svg></span></a>
<a class="btn" style="left:839px;top:1000px;width:127px">Shop Now<span class="arr"><svg viewBox="0 0 16 16" fill="none" stroke="#3c3c3b" stroke-width="1.6"><path d="M2 8h11M9 4l4 4-4 4"/></svg></span></a>

<!-- ===== BEST SELLERS ===== -->
<section class="bests"></section>
<div class="eyebrow" style="top:1156px">Products</div>
<h2 class="sec-title display" style="top:1175px">Our Best Sellers</h2>

<div class="ph" role="img" aria-label="Woman stacking bags of feed in a warehouse" style="left:-46px;top:1250px;width:416px;height:440px;border-radius:50%;background:linear-gradient(160deg,#e8ece8,#b7c4c8 45%,#3a9ab8 75%,#d86a8a);border:6px solid var(--white)"></div>
<div class="ph" style="left:-50px;top:1236px;width:434px;height:466px;border-radius:50%;border:3px solid var(--orange)"></div>

<div class="card" style="left:466px" role="img" aria-label="Premium koi pellets with a black scoop" >
  <div style="position:absolute;inset:0;background:linear-gradient(180deg,#8a5a3e,#6b412c 60%,#3f3a38)"></div>
  <svg class="heart" width="20" height="18" viewBox="0 0 20 18" fill="none" stroke="#fff" stroke-width="1.6"><path d="M10 16S2 11 2 6a4 4 0 018-1 4 4 0 018 1c0 5-8 10-8 10z"/></svg>
  <div class="tag display">Best Seller</div>
  <div class="name">Premium Koi Pellets</div>
  <div class="desc">(High-protein, promotes vibrant colors)</div>
  <a class="btn" style="left:18px;top:313px;width:166px">Discover More<span class="arr"><svg viewBox="0 0 16 16" fill="none" stroke="#3c3c3b" stroke-width="1.6"><path d="M2 8h11M9 4l4 4-4 4"/></svg></span></a>
</div>
<div class="card" style="left:807px" role="img" aria-label="Golden goldfish flakes close-up">
  <div style="position:absolute;inset:0;background:linear-gradient(180deg,#f2a12e,#e6911e 60%,#5a4a3a)"></div>
  <svg class="heart" width="20" height="18" viewBox="0 0 20 18" fill="none" stroke="#fff" stroke-width="1.6"><path d="M10 16S2 11 2 6a4 4 0 018-1 4 4 0 018 1c0 5-8 10-8 10z"/></svg>
  <div class="tag display">New Arrival</div>
  <div style="position:absolute;right:26px;top:226px;font-size:11px;color:#fff">5.0</div>
  <div class="name">Goldfish Flakes</div>
  <div class="desc">(Easy-to-digest daily feed)</div>
  <a class="btn" style="left:18px;top:313px;width:178px">Discover More<span class="arr"><svg viewBox="0 0 16 16" fill="none" stroke="#3c3c3b" stroke-width="1.6"><path d="M2 8h11M9 4l4 4-4 4"/></svg></span></a>
</div>
<div class="card" style="left:1148px" role="img" aria-label="Chicken starter feed">
  <div style="position:absolute;inset:0;background:linear-gradient(180deg,#a87a55,#6a4a38 60%,#3f3a38)"></div>
  <div class="tag display">Starter</div>
  <div class="name">Chick Crumbs</div>
  <div class="desc">(Healthy start)</div>
  <a class="btn" style="left:18px;top:313px;width:166px">Discover More</a>
</div>
<span class="circ-nav" style="left:1064px;top:1680px;border:2px solid #4a4a49"><svg width="12" height="12" viewBox="0 0 12 12" fill="none" stroke="#3c3c3b" stroke-width="1.8"><path d="M8 2L4 6l4 4"/></svg></span>
<span class="circ-nav" style="left:1106px;top:1680px;background:#555"><svg width="12" height="12" viewBox="0 0 12 12" fill="none" stroke="#fff" stroke-width="1.8"><path d="M4 2l4 4-4 4"/></svg></span>

<!-- ===== PROMO ===== -->
<div class="promo">
  <div class="ph" role="img" aria-label="Scoop lifting grain pellets from a bowl" style="left:-6px;top:-20px;width:370px;height:300px;border-radius:0 50% 50% 0;background:radial-gradient(circle at 45% 55%,#7a6a58,#a89a88 50%,#d6cfc4)"></div>
  <svg class="abs" style="left:150px;top:0" width="220" height="282" viewBox="0 0 220 282" fill="none" stroke="var(--orange)" stroke-width="3"><path d="M60 278C200 260 230 80 120 6"/></svg>
  <div class="display" style="position:absolute;left:356px;top:16px;width:600px;font-size:30px;color:var(--orange);text-align:center;left:210px">Buy 2, Get 1</div>
  <div class="display" style="position:absolute;left:210px;top:52px;width:600px;font-size:32px;color:#fff;text-align:center">Free on Chicken Feed</div>
  <svg class="abs" style="left:433px;top:112px" width="370" height="52" viewBox="0 0 370 52"><path d="M0 0H370L352 26 370 52H0L18 26Z" fill="#fff"/></svg>
  <div style="position:absolute;left:474px;top:122px;font-size:14px;font-weight:600;color:var(--dark)">Free Shipping on Orders Over <span style="font-size:26px;font-weight:600;vertical-align:-4px;margin-left:10px">€50</span></div>
  <div style="position:absolute;left:210px;top:174px;width:600px;text-align:center;font-size:14px;color:#fff">Limited time offer for all pond fish products</div>
  <a class="btn" style="left:549px;top:222px;width:127px">Shop Now<span class="arr"><svg viewBox="0 0 16 16" fill="none" stroke="#3c3c3b" stroke-width="1.6"><path d="M2 8h11M9 4l4 4-4 4"/></svg></span></a>
</div>
<span class="circ-nav" style="left:77px;top:1897px;background:var(--orange)"><svg width="12" height="12" viewBox="0 0 12 12" fill="none" stroke="#fff" stroke-width="1.8"><path d="M8 2L4 6l4 4"/></svg></span>
<span class="circ-nav" style="left:1090px;top:1897px;background:var(--orange)"><svg width="12" height="12" viewBox="0 0 12 12" fill="none" stroke="#fff" stroke-width="1.8"><path d="M4 2l4 4-4 4"/></svg></span>

<!-- ===== THREE BANNERS ===== -->
<div class="banner" style="left:0;width:302px;background:linear-gradient(90deg,#8e8e8c,#a5a5a3)">
  <div class="ph" role="img" aria-label="Bucket of nuts and grain" style="left:150px;top:0;width:152px;height:180px;border-radius:0 0 0 60%;background:linear-gradient(160deg,#6a8a9a,#c9a26a)"></div>
  <div class="display" style="position:absolute;left:6px;top:62px;font-size:22px;line-height:34px;color:#fff">Nutrient-<br>ed</div>
  <div style="position:absolute;left:0;top:145px;font-size:11px;color:#fff">nts for healthy growth</div>
  <div style="position:absolute;left:0;top:170px;font-size:11px;color:var(--orange)">t Now ➔</div>
  <div style="position:absolute;right:8px;bottom:8px;font-size:10px;color:#fff">Brenvik</div>
</div>
<div class="banner" style="left:334px;width:532px;height:231px;background:linear-gradient(90deg,#8d8d8b,#eeeeec)">
  <svg class="abs" style="left:0;top:0" width="532" height="231" viewBox="0 0 532 231"><path d="M20 30C120 0 290 10 330 60C360 110 330 200 240 222C150 236 30 230 10 170C-5 120-10 45 20 30Z" fill="var(--orange)"/></svg>
  <div class="ph" role="img" aria-label="Delivery woman in red cap carrying a parcel" style="left:330px;top:12px;width:190px;height:219px;border-radius:50% 50% 0 0;background:linear-gradient(180deg,#e8d9cc,#d82a24 45%,#c8a27a)"></div>
  <div style="position:absolute;right:14px;top:12px;font-size:14px;font-weight:700;color:var(--dark)">Brenvik</div>
  <div class="display" style="position:absolute;left:40px;top:56px;width:280px;text-align:center;font-size:23px;line-height:28px;color:var(--white)">Fast Delivery Across the Netherlands</div>
  <div style="position:absolute;left:40px;top:124px;width:280px;text-align:center;font-size:11px;color:#fff">Get your feed delivered within 24 hours</div>
  <div style="position:absolute;left:40px;top:156px;width:280px;text-align:center;font-size:13px;font-weight:600;color:var(--dark)">Grab It Now ➔</div>
</div>
<div class="banner" style="left:897px;width:303px;background:linear-gradient(90deg,#a8a8a6,#9a9a98)">
  <div class="ph" role="img" aria-label="Farmer standing in front of a barn" style="left:0;top:30px;width:120px;height:188px;border-radius:0 60% 0 0;background:linear-gradient(180deg,#7a8a6a,#4a5a4a)"></div>
  <div style="position:absolute;left:10px;top:12px;font-size:10px;color:#fff">Brenvik</div>
  <div class="display" style="position:absolute;left:178px;top:78px;font-size:22px;line-height:28px;color:#fff;white-space:nowrap">Trusted by<br>&nbsp;&nbsp;&nbsp;&nbsp;&nbsp;Pond</div>
  <div style="position:absolute;left:180px;top:140px;font-size:11px;color:#fff;white-space:nowrap">Recommended by pro</div>
  <div style="position:absolute;left:248px;top:170px;font-size:11px;color:var(--orange);white-space:nowrap">Grab It</div>
</div>
<span class="abs" style="left:575px;top:2379px;width:11px;height:11px;border-radius:50%;background:#d3d3d3"></span>
<span class="abs" style="left:594px;top:2379px;width:11px;height:11px;border-radius:50%;background:var(--orange)"></span>
<span class="abs" style="left:613px;top:2379px;width:11px;height:11px;border-radius:50%;background:#d3d3d3"></span>

<!-- ===== USPs ===== -->
<section class="usp"></section>
<div class="eyebrow" style="top:2513px;color:#fff">USPs</div>
<h2 class="sec-title display" style="top:2532px;color:#fff">Our Best Sellers Products</h2>

<div class="usp-card" style="left:139px;top:2676px"><span class="ico"><svg width="20" height="14" viewBox="0 0 20 14" fill="#3c3c3b"><rect x="0" y="1" width="12" height="9"/><path d="M12 4h4l3 3v3h-7z"/><circle cx="4" cy="12" r="2"/><circle cx="15" cy="12" r="2"/></svg></span><h4>Fast Delivery</h4><small>Orders shipped within 24h</small></div>
<div class="usp-card" style="left:455px;top:2676px"><span class="ico"><svg width="16" height="20" viewBox="0 0 16 20" fill="none" stroke="#3c3c3b" stroke-width="2"><circle cx="8" cy="7" r="5"/><path d="M4 11l-2 8 6-3 6 3-2-8"/></svg></span><h4>Top Quality Feed</h4><small>Tested by nutrition experts</small></div>
<div class="usp-card" style="left:139px;top:2766px"><span class="ico"><svg width="18" height="18" viewBox="0 0 18 18" fill="#3c3c3b"><circle cx="9" cy="5" r="4"/><path d="M1 18c0-6 16-6 16 0z"/></svg></span><h4>Loved by Professionals</h4><small>Trusted by farms &amp; breeders</small></div>
<div class="usp-card" style="left:455px;top:2766px"><span class="ico"><svg width="20" height="14" viewBox="0 0 20 14" fill="none" stroke="#3c3c3b" stroke-width="2"><rect x="1" y="1" width="18" height="12" rx="2"/><path d="M1 5h18"/></svg></span><h4>Secure Payments</h4><small>Safe checkout guaranteed</small></div>
<a class="btn" style="left:139px;top:2864px;width:177px">Discover More<span class="arr"><svg viewBox="0 0 16 16" fill="none" stroke="#3c3c3b" stroke-width="1.6"><path d="M2 8h11M9 4l4 4-4 4"/></svg></span></a>

<div class="ph" role="img" aria-label="Shop assistant holding a clipboard beside feed shelves" style="left:796px;top:2618px;width:334px;height:334px;border-radius:50%;background:linear-gradient(160deg,#d8d2c4,#8a7a6a 50%,#2a3450);border:4px solid #fff"></div>
<div class="ph" style="left:794px;top:2604px;width:342px;height:352px;border-radius:50%;border:3px solid var(--orange)"></div>

<!-- ===== SEO ===== -->
<svg class="abs" style="left:0;top:3000px" width="1200" height="260" viewBox="0 0 1200 260" fill="none" stroke="#fbe2c0" stroke-width="3" aria-hidden="true">
  <path d="M-40 10C80 40 90 200-20 230"/><path d="M1240 110C1120 130 1110 260 1230 280"/>
</svg>
<h2 class="display" style="position:absolute;left:0;top:3070px;width:1200px;text-align:center;font-size:44px;color:var(--brown)">Healthy Feed, Happy Animals</h2>
<p style="position:absolute;left:198px;top:3146px;width:804px;text-align:center;font-size:12.5px;line-height:17px">Lorem ipsum dolor sit amet, consectetur adipiscing elit. Brenvik.nl biedt een breed assortiment aan hoogwaardig vis- en kippenvoer. Onze producten zijn zorgvuldig samengesteld om de gezondheid, groei en vitaliteit van uw dieren te ondersteunen. Of u nu op zoek bent naar professioneel vijvervoer, dagelijks kippenvoer of handige accessoires – bij Brenvik.nl vindt u alles op één plek. Wij leveren snel door heel Nederland, zodat uw vissen en kippen altijd het beste krijgen, precies wanneer ze het nodig hebben.</p>
<a class="btn" style="left:536px;top:3242px;width:127px">Shop Now<span class="arr"><svg viewBox="0 0 16 16" fill="none" stroke="#3c3c3b" stroke-width="1.6"><path d="M2 8h11M9 4l4 4-4 4"/></svg></span></a>

<!-- ===== FOOTER ===== -->
<footer class="footer">
  <div class="ph" role="img" aria-label="Dark underwater scene with koi fish" style="left:0;top:0;width:1200px;height:431px;background:linear-gradient(180deg,#4a4334,#2f2c26 60%,#262420)"></div>
  <svg class="abs" style="left:0;top:0" width="1200" height="150" viewBox="0 0 1200 150" aria-hidden="true">
    <path d="M0 0H1200V40C1000 10 860 30 700 70C520 115 340 90 180 60C90 45 30 55 0 70Z" fill="var(--white)"/>
    <path d="M0 70C30 55 90 45 180 60C340 90 520 115 700 70C860 30 1000 10 1200 40V95C1000 60 860 80 700 120C520 160 340 130 180 105C90 92 30 100 0 110Z" fill="var(--orange)"/>
  </svg>
  <div class="logo" style="left:68px;top:196px;font-size:62px"><span class="dot" style="width:56px;height:56px;border-width:7px"></span>Brenvik</div>
  <p style="position:absolute;left:68px;top:272px;width:252px;font-size:9.5px;line-height:12px;color:#fff">Brenvik.nl is your trusted online store for high-quality fish and chicken feed in the Netherlands. We provide a carefully selected range of nutritious products designed to keep your animals healthy, active, and thriving.</p>

  <div class="fcol" style="position:absolute;left:430px;top:207px"><h5>Main Links</h5><a>Home</a><a>Category</a><a>Products</a><a>USPs</a><a>Contact Us</a></div>

  <div class="fcol" style="position:absolute;left:640px;top:207px;width:250px"><h5>Contact Us</h5>
    <li style="display:flex;gap:12px"><svg width="9" height="12" viewBox="0 0 9 12" fill="#fff"><path d="M4.5 0A4.5 4.5 0 000 4.5C0 8 4.5 12 4.5 12S9 8 9 4.5A4.5 4.5 0 004.5 0z"/></svg><span>Lindegracht 12 1016 KP Amsterdam<br>The Netherlands</span></li>
    <li style="display:flex;gap:12px;margin-top:18px"><svg width="10" height="10" viewBox="0 0 10 10" fill="#fff"><path d="M2 0l2 2.5L3 4c.7 1.4 1.6 2.3 3 3l1.5-1L10 8l-1 2C4 10 0 6 0 1z"/></svg><span>+31 6 9876 5432</span></li>
    <li style="display:flex;gap:12px;margin-top:18px"><svg width="10" height="8" viewBox="0 0 10 8" fill="#fff"><rect width="10" height="8" rx="1"/></svg><span>info@brenvik.nl</span></li>
  </div>

  <div class="fcol" style="position:absolute;left:937px;top:207px"><h5>Subscribe Newsletter</h5>
    <div class="field">Email</div>
    <div class="field" style="height:58px">Message</div>
    <a class="btn" style="position:relative;top:6px;width:127px;display:flex;font-size:14px;color:var(--dark);margin:0">Submit<span class="arr"><svg viewBox="0 0 16 16" fill="none" stroke="#3c3c3b" stroke-width="1.6"><path d="M2 8h11M9 4l4 4-4 4"/></svg></span></a>
  </div>

  <div style="position:absolute;left:0;top:431px;width:1200px;height:28px;background:#1e1e1d;color:#fff;font-size:10px;text-align:center;line-height:28px">© 2025 Brenvik.nl | All rights reserved.</div>
</footer>

</body>
</html>
```